Specialised investor in e-mobility and energy wants business card design

We need a business card design that fits our existing corporate design. <The look and feel must be 'sharp'/'clean', dynamic, communicate momentum, professionalism etc (as one would imagine from a firm in the financial sector). We like the idea of a reverse-side of the card that includes the logo, and the name and contact details on the other. We expect the deliverable to be whatever format might be required to be able to get cards printed directly by a service such as kelmo press. Our website is www.zub.capital

```html
<!DOCTYPE html>
<html lang="en">
<head>
<meta charset="utf-8">
<title>ZUB Capital – Business Card</title>
<link href="https://fonts.googleapis.com/css2?family=Questrial&display=swap" rel="stylesheet">
<style>
  :root {
    --green-dark: #2f5424;
    --green-deep: #1f3f14;
    --green-light: #86b84a;
    --white: #ffffff;
    --backdrop: #e3e4e6;
    --rule: rgba(134, 184, 74, 0.55);
  }
  * { margin: 0; padding: 0; box-sizing: border-box; }
  html, body {
    width: 1200px; height: 800px; overflow: hidden;
    background: var(--backdrop);
    font-family: "Questrial", "Century Gothic", sans-serif;
  }
  .sheet {
    position: relative; width: 1200px; height: 800px;
    display: flex; align-items: center; justify-content: center; gap: 60px;
  }
  .card {
    position: relative; width: 525px; height: 300px;
    background: var(--white);
    box-shadow: 0 6px 18px rgba(0,0,0,0.15);
    overflow: hidden;
  }
  .card-shape { position: absolute; inset: 0; width: 100%; height: 100%; }

  /* Logo side */
  .brand {
    position: absolute; display: flex; align-items: center; gap: 12px;
    font-size: 46px; letter-spacing: 0.5px; line-height: 1; white-space: nowrap;
  }
  .brand-dot { width: 14px; height: 14px; border-radius: 50%; flex: none; }
  .card--front .brand { left: 42px; top: 120px; color: var(--white); }
  .card--front .brand-dot { background: var(--white); }
  .website-tag {
    position: absolute; right: 26px; top: 36px;
    font-size: 13px; letter-spacing: 5px; color: var(--green-dark);
  }

  /* Contact side */
  .card--back .brand { left: 40px; top: 48px; color: var(--green-dark); }
  .card--back .brand-dot { background: var(--green-light); }
  .contact {
    position: absolute; right: 26px; top: 168px; width: 330px;
    text-align: right; color: var(--white);
  }
  .contact-role { font-size: 13px; }
  .contact-name { font-size: 16px; color: var(--green-light); letter-spacing: 0.5px; margin-bottom: 4px; }
  .contact-line {
    display: flex; justify-content: flex-end; align-items: center; gap: 6px;
    font-size: 12.5px; line-height: 18px; white-space: nowrap;
  }
  .contact-line svg { width: 11px; height: 11px; flex: none; }
  .contact-rule { border-top: 1px solid var(--rule); margin: 6px 0 5px; }
  .company-line .company { color: var(--green-light); margin-right: 4px; }
</style>
</head>
<body>
<main class="sheet">

  <!-- Logo side -->
  <section class="card card--front" aria-label="Business card, logo side">
    <svg class="card-shape" viewBox="0 0 525 300" preserveAspectRatio="none" aria-hidden="true">
      <defs>
        <linearGradient id="frontGreen" x1="0" y1="1" x2="1" y2="0">
          <stop offset="0" stop-color="#173a0c"/>
          <stop offset="1" stop-color="#3a5e2c"/>
        </linearGradient>
      </defs>
      <path d="M0,0 L120,0 Q400,40 470,300 L0,300 Z" fill="#86b84a"/>
      <path d="M0,0 L100,0 Q375,48 448,300 L0,300 Z" fill="url(#frontGreen)"/>
    </svg>
    <div class="brand"><span class="brand-dot"></span><span class="brand-name">ZUB Capital</span></div>
    <div class="website-tag">www.zub.capital</div>
  </section>

  <!-- Contact side -->
  <section class="card card--back" aria-label="Business card, contact side">
    <svg class="card-shape" viewBox="0 0 525 300" preserveAspectRatio="none" aria-hidden="true">
      <path d="M0,165 Q250,70 525,150 L525,300 L0,300 Z" fill="#86b84a"/>
      <path d="M0,180 Q250,88 525,165 L525,300 L0,300 Z" fill="#2f5424"/>
    </svg>
    <div class="brand"><span class="brand-dot"></span><span class="brand-name">ZUB Capital</span></div>
    <div class="contact">
      <div class="contact-role">Partner</div>
      <div class="contact-name">MARCUS ELLWOOD</div>
      <div class="contact-line">+1 555 014 8220
        <svg viewBox="0 0 12 12"><rect x="3" y="0.5" width="6" height="11" rx="1" fill="none" stroke="#86b84a"/></svg>
      </div>
      <div class="contact-line">marcus@zub.capital
        <svg viewBox="0 0 12 12"><rect x="1" y="2.5" width="10" height="7" fill="#86b84a"/><path d="M1,2.5 L6,6.5 L11,2.5" fill="none" stroke="#2f5424"/></svg>
      </div>
      <div class="contact-line">www.zub.capital
        <svg viewBox="0 0 12 12"><circle cx="6" cy="6" r="5" fill="none" stroke="#86b84a"/><path d="M1,6 H11 M6,1 V11" stroke="#86b84a"/></svg>
      </div>
      <div class="contact-rule"></div>
      <div class="contact-line company-line"><span class="company">ZUB Capital Group</span> Ashford Quay, Linmouth
        <svg viewBox="0 0 12 12"><path d="M6,11.5 L2.2,6 A4,4 0 1 1 9.8,6 Z" fill="#86b84a"/><circle cx="6" cy="4.4" r="1.5" fill="#2f5424"/></svg>
      </div>
    </div>
  </section>

</main>
</body>
</html>
```